Company or website name
- dalewintham.com
- Links to the website
- Vita Forge
- Describe your company and organization and target audience
- Founded by celebrity personal trainer and media personality Dale Wintham, Vita Forge provides high quality on-site fitness and wellness classes, and personal trainers for businesses and residential gyms throughout New York City. Our target audience are residents of high end buildings in NYC, that expect excellence and luxury
- The design should have the following
- This is a 24"x36" Poster for a complimentary event at a high end building. I would like the poster to look high end, luxury and simple and chique. The words should be clear and easy to read. It would be great to have a final copy that we can send to the printer and one which we can edit for future events Here is the text: The Halcott Spires Gym Complimentary Fitness & Wellness Event Complimentary Yoga, Pilates & Interval Training Bootcamp Classes PLUS: 30 Minute Private Training Sessions *Kids Karate Classes Also Available Saturday May 18th, 25th & June 1st Time: 9:00am - 12:15pm Halcott Spires Gym Schedule: 9:00am - 9:30am Yoga 9:45am - 10:15am Interval Training Bootcamp 11:45am -12:15pm Pilates 9:00am - 12:00pm Private Training Sessions Special Introductory Rate on Future Packages During Promotion www.Vitaforge.tv Info@vitaforge.tv
- Other Facts

```html
<!DOCTYPE html>
<html lang="en">
<head>
<meta charset="utf-8">
<title>The Halcott Spires Gym – Complimentary Fitness &amp; Wellness Event</title>
<link rel="stylesheet" href="https://fonts.googleapis.com/css2?family=Roboto+Condensed:ital,wght@0,400;0,700;1,700&display=swap">
<style>
  :root {
    --page: #ffffff;
    --ink: #0a0a0a;
    --brand-blue: #1b5ba3;
    --event-green: #4f6b2d;
    --text-light: #ffffff;
    --photo-dark: #1c1c1c;
    --photo-warm: #6b5646;
    --wave-green: #2f3b16;
  }
  * { margin: 0; padding: 0; box-sizing: border-box; }
  html, body {
    width: 1200px; height: 961px; overflow: hidden;
    background: var(--page);
    font-family: "Roboto Condensed", "Arial Narrow", sans-serif;
  }
  .poster {
    position: absolute; left: 282px; top: 0; width: 641px; height: 961px;
    background: var(--ink); color: var(--text-light);
  }
  .poster-top { position: absolute; left: 0; top: 0; width: 100%; height: 27px; background: var(--page); }
  .header-band {
    position: absolute; left: 0; top: 27px; width: 100%; height: 93px;
    background: var(--brand-blue); text-align: center;
  }
  .header-band .title {
    font-weight: 700; font-size: 38px; letter-spacing: 0.5px; line-height: 1;
    padding-top: 13px;
  }
  .header-band .rule { height: 2px; background: var(--text-light); margin: 8px 0 0; }
  .header-band .subtitle { font-weight: 400; font-size: 25px; line-height: 1; padding-top: 6px; letter-spacing: 0.3px; }
  .feature-area {
    position: absolute; left: 0; top: 125px; width: 100%; height: 622px;
    background: radial-gradient(ellipse at 70% 55%, var(--wave-green) 0%, var(--ink) 65%);
  }
  .athlete-photo {
    position: absolute; left: 30px; top: 130px; width: 215px; height: 797px;
    background: linear-gradient(180deg, var(--photo-warm) 0%, var(--photo-dark) 45%, var(--photo-warm) 80%, var(--photo-dark) 100%);
    border-radius: 40px 40px 10px 10px; opacity: 0.85;
  }
  .contact-vertical {
    position: absolute; left: 29px; top: 723px;
    transform: rotate(-90deg); transform-origin: left top;
    font-weight: 700; font-size: 17px; white-space: nowrap; word-spacing: 14px;
  }
  .offer { position: absolute; right: 26px; text-align: right; line-height: 1; }
  .offer-classes { top: 160px; font-weight: 700; font-size: 26px; }
  .offer-classes span { display: block; margin-bottom: 6px; }
  .offer-plus { top: 303px; font-weight: 700; font-style: italic; font-size: 32px; }
  .offer-plus span { display: block; margin-bottom: 5px; }
  .offer-rate { top: 443px; font-weight: 700; font-style: italic; font-size: 19px; }
  .offer-rate span { display: block; margin-bottom: 11px; }
  .divider { position: absolute; right: 0; height: 3px; background: var(--text-light); }
  .divider-one { top: 276px; width: 425px; }
  .divider-two { top: 422px; width: 323px; }
  .divider-three { top: 538px; width: 350px; }
  .brand-mark {
    position: absolute; left: 225px; top: 585px; width: 400px;
    display: flex; align-items: center; justify-content: center; gap: 14px;
  }
  .brand-mark .dot { width: 22px; height: 22px; border-radius: 50%; background: var(--text-light); }
  .brand-mark .name { font-weight: 700; font-size: 52px; letter-spacing: 2px; text-transform: uppercase; }
  .schedule-band {
    position: absolute; left: 0; top: 747px; width: 100%; height: 191px;
    background: var(--event-green);
  }
  .schedule {
    position: absolute; right: 20px; top: 18px; text-align: right;
    font-weight: 700; font-size: 17.5px; line-height: 29px; white-space: nowrap;
  }
  .schedule em { font-style: italic; }
  .poster-bottom { position: absolute; left: 0; top: 938px; width: 100%; height: 23px; background: var(--ink); }
</style>
</head>
<body>
<main class="poster">
  <div class="poster-top"></div>

  <header class="header-band">
    <h1 class="title">THE HALCOTT SPIRES GYM</h1>
    <div class="rule"></div>
    <p class="subtitle">COMPLIMENTARY FITNESS &amp; WELLNESS EVENT</p>
  </header>

  <section class="feature-area"></section>
  <div class="athlete-photo" role="img" aria-label="Photo of a female athlete in black sportswear throwing a punch mid-jump"></div>

  <p class="contact-vertical">www.Vitaforge.tv Info@vitaforge.tv</p>

  <p class="offer offer-classes"><span>COMPLIMENTARY YOGA,</span><span>PILATES &amp; INTERVAL TRAINING</span><span>BOOTCAMP CLASSES</span></p>
  <div class="divider divider-one"></div>

  <p class="offer offer-plus"><span>PLUS:</span><span>30 MINUTE PRIVATE</span><span>TRAINING SESSIONS</span></p>
  <div class="divider divider-two"></div>

  <p class="offer offer-rate"><span>Special Introductory Rate</span><span>on Future Packages</span><span>During Promotion</span></p>
  <div class="divider divider-three"></div>

  <div class="brand-mark">
    <span class="dot"></span>
    <span class="name">Vita Forge</span>
  </div>

  <section class="schedule-band">
    <div class="schedule">
      <div>SCHEDULE: Yoga <em>9:45am - 10:15am</em></div>
      <div>Interval Training Bootcamp <em>11:45am -12:15pm</em></div>
      <div>Halcott Spires Gym Schedule: <em>9:00am - 9:30am</em></div>
      <div>Pilates <em>9:00am - 12:00pm</em></div>
      <div>*Kids Karate Classes Also Available</div>
      <div><em>Saturday May 18th, 25th &amp; June 1st Time: 9:00am - 12:15pm</em></div>
    </div>
  </section>

  <div class="poster-bottom"></div>
</main>
</body>
</html>
```